House-share and Room Rental Website (With Focus on the Bedroom Landing Page)

Looking for website design for our House-share (executive accommodation) and room rental business.

Our company name is: Lodgivo could also be written as LodGivo or lodgivo. Either is fine .. just looking for a nice clean catchy logo to go with the design.

EXAMPLES
These are examples of other websites in this field that are doing well. this is a kind of baseline.
https://nestpartners-example.com.au/
https://www.bunkora-example.com/
https://www.dwelzy-example.com/
https://www.habiquo-example.net/
https://www.cohabiscout-example.com.au/

Our business model is to rent rooms to people looking for high-quality accommodation. We fill the gap between those looking to rent rooms and those with rooms to rent. However, our model is slightly different from those already on the market as we looking to fill a massive gap in the market delivering upmarket rooms for rent.(Executive Accommodation) also in the back end will be coupled with a self management process in the back end.

We offer executive style accommodation that stands out above the rest. With special extras like fire safety.. and management processes that create happier homes. We are looking for a web design package that can help us grow and scale our business. We need a design that is captivating

Our MAIN focus is having a room landing page that stands out from the rest... The core of our business will rely on the promotion of the rooms in a share house... so the whole design relies on the BEDROOM landing page to drive results.

Target Market(s)

We have 2 markets we are aiming at ... the first market is people offering rooms to rent who want the highest rental return. The second market is people looking to rent safe, high-quality rooms, in houses that are well managed and looked after.

Industry/Entity Type

Share Economy

Logo Text

LodGivo

Number of Pages Required

5+ page

Font styles to use
Sans Serif

Colors
3276b5

Requirements
Must have
• A messaging system whereby we can create direct communication between those offering rooms and those looking for rooms.
• A call to action that says " Schedule an Inspection"
• Landing page for promoting rooms
• A home page for showing stock.
• Profile page for those selling rooms
• Profile page for those looking for rooms.
• A scheduling calendar for booking inspections
Nice to have
• Pages where new residents can lock in a room.. pay bond and rents.. and sign contracts
• Notifications
• SMS capabilities in the backend.
Should not have
• No script or handwriting fonts.

```html
<!DOCTYPE html>
<html lang="en">
<head>
<meta charset="utf-8">
<title>Lodgivo – Bedrooms</title>
<link href="https://fonts.googleapis.com/css2?family=Montserrat:wght@500;600;700;800&family=Lato:wght@400;700&family=Roboto:wght@400;500;700&display=swap" rel="stylesheet">
<style>
:root{
  --brand-red:#e3151a;
  --sky:#059fe3;
  --sky-deep:#0a8fd9;
  --chat-blue:#1b8ff0;
  --bubble-blue:#4cb3f5;
  --bubble-grey:#c9c9d1;
  --ink:#222;
  --muted:#777;
  --dark:#2b2b2b;
  --panel:#ececec;
  --white:#fff;
}
*{box-sizing:border-box;margin:0;padding:0}
html,body{width:1200px;height:1200px;overflow:hidden;background:var(--white)}
body{position:relative;font-family:'Lato',sans-serif;color:var(--ink)}
.abs{position:absolute}

/* header */
.site-header{left:0;top:0;width:1200px;height:77px}
.brand{left:192px;top:10px;font-family:'Montserrat',sans-serif;font-weight:800;font-size:42px;color:var(--brand-red);letter-spacing:-1px}
.nav{font-family:'Montserrat',sans-serif;font-weight:700;font-size:10px;letter-spacing:.9px;color:#222;top:37px}

/* search band */
.search-band{left:0;top:77px;width:1200px;height:60px;background:var(--sky)}
.search-box{left:173px;top:12px;width:739px;height:38px;background:var(--white);display:flex;font-family:'Montserrat',sans-serif;font-size:10px;font-weight:600;color:#333}
.field{display:flex;align-items:center;border-right:1px solid #ddd;position:relative}
.field.keywords{width:325px;padding-left:28px;gap:6px;font-weight:500;letter-spacing:.5px}
.field.select{width:170px;justify-content:center}
.field.select.style{width:180px}
.caret{position:absolute;right:20px;top:17px;border:4px solid transparent;border-top:5px solid #222}
.go{width:64px;background:var(--dark);color:#fff;display:flex;align-items:center;justify-content:center;font-size:9px;font-weight:700}

/* hero */
.hero{left:0;top:137px;width:1200px;height:447px;background:radial-gradient(ellipse at 50% 40%,#d9c98a 0%,#b79e5a 45%,#6d5a2f 100%)}
.listing-card{left:498px;top:108px;width:328px;height:177px;background:#fbfbfb;border-radius:10px}
.listing-card::after{content:"";position:absolute;left:193px;bottom:-7px;border:7px solid transparent;border-bottom:0;border-top:7px solid #fbfbfb}
.listing-photo{left:14px;top:17px;width:152px;height:143px;border-radius:8px;background:linear-gradient(180deg,#b9cfe0 0%,#8d9aa1 55%,#5c5a4e 100%)}
.price{left:180px;top:33px;font-family:'Montserrat',sans-serif;font-weight:700;font-size:15px}
.listing-title{left:180px;top:58px;font-family:'Montserrat',sans-serif;font-weight:700;font-size:12.5px;line-height:16px}
.listing-addr{left:180px;top:107px;font-size:8px;color:#333}
.details{left:181px;top:131px;font-size:9.5px;color:#222}
.details::after{content:"";display:inline-block;margin-left:7px;border:3px solid transparent;border-left:4px solid #222;border-right:0}
.tag-rent{left:251px;top:153px;width:73px;height:20px;border-radius:10px;background:var(--dark);color:#fff;font-size:8px;font-weight:700;display:flex;align-items:center;justify-content:center}
.dots{left:582px;top:433px;display:flex;gap:4px}
.dots span{width:12px;height:12px;border-radius:50%;background:rgba(255,255,255,.45)}
.dots span.on{background:#fff}

/* features */
.features{left:0;top:584px;width:1200px;height:254px;background:var(--sky)}
.feature-ring{width:87px;height:87px;border:3px solid #fff;border-radius:50%;display:flex;align-items:center;justify-content:center}
.feature-title{font-family:'Montserrat',sans-serif;font-weight:700;font-size:15px;color:#fff;text-align:center;width:300px}
.feature-text{font-size:11.5px;color:#fff;text-align:center;width:300px;line-height:21px}

/* newest */
.section-title{left:0;width:1206px;top:909px;text-align:center;font-family:'Roboto',sans-serif;font-weight:500;font-size:21px;letter-spacing:-.3px}
.section-sub{left:0;width:1206px;top:940px;text-align:center;font-size:12.5px;color:var(--muted);letter-spacing:.4px}
.room-photo{top:997px;height:203px}
.tag-green{left:357px;top:14px;width:57px;height:18px;background:#3db54a;color:#fff;font-size:7.5px;font-weight:700;display:flex;align-items:center;justify-content:center}

/* chat */
.chat{left:838px;top:698px;width:346px;height:502px;background:var(--white);box-shadow:0 0 8px rgba(0,0,0,.12)}
.chat-head{left:0;top:0;width:346px;height:65px;background:var(--chat-blue);border-radius:6px 6px 0 0}
.chat-title{left:21px;top:20px;font-family:'Roboto',sans-serif;font-weight:700;font-size:21px;color:#fff;letter-spacing:-.2px}
.chat-body{left:0;top:65px;width:346px;height:312px;background:var(--panel)}
.bubble{font-size:13.5px;padding:0 12px;height:39px;display:flex;align-items:center;border-radius:3px}
.bubble.them{background:var(--bubble-grey);color:#222;left:19px}
.bubble.me{background:var(--bubble-blue);color:#fff;right:36px}
.scroll-track{left:327px;top:76px;width:7px;height:292px;border-radius:4px;background:#fff}
.scroll-thumb{left:327px;top:76px;width:7px;height:192px;border-radius:4px;background:var(--chat-blue)}
.chat-input{left:13px;top:416px;width:319px;height:63px;border:2px solid #ddd;border-radius:4px}
.placeholder{left:14px;top:21px;font-size:12.5px;font-style:italic;color:#777}
.send{left:268px;top:3px;width:46px;height:53px;background:var(--chat-blue);border:2px solid #0d5fb0;border-radius:4px;display:flex;align-items:center;justify-content:center}
</style>
</head>
<body>

<header class="abs site-header">
  <div class="abs brand">Logo</div>
  <span class="abs nav" style="left:370px">HOME</span>
  <span class="abs nav" style="left:443px">ABOUT US</span>
  <span class="abs nav" style="left:540px">CONTACT US</span>
  <span class="abs nav" style="left:649px">BEDROOMS</span>
  <span class="abs nav" style="left:753px">CHILD ROOMS</span>
  <span class="abs nav" style="left:872px">BLOG</span>
  <span class="abs nav" style="left:1011px;top:35px">LOGIN/REGISTER</span>
</header>

<section class="abs search-band">
  <div class="abs search-box">
    <div class="field keywords">
      <svg width="10" height="10" viewBox="0 0 10 10"><circle cx="4" cy="4" r="3" fill="none" stroke="#111" stroke-width="1.6"/><line x1="6.2" y1="6.2" x2="9.3" y2="9.3" stroke="#111" stroke-width="1.8"/></svg>
      Keywords
    </div>
    <div class="field select"><span style="margin-right:30px">Select Room</span><i class="caret"></i></div>
    <div class="field select style"><span style="margin-right:20px">Room Style</span><i class="caret"></i></div>
    <div class="go">GO</div>
  </div>
</section>

<section class="abs hero" role="img" aria-label="Photo of a furnished classic bedroom with a large bed, dresser and TV">
  <article class="abs listing-card">
    <div class="abs listing-photo" role="img" aria-label="Photo of a modern two-storey family house"></div>
    <div class="abs price">$125,799</div>
    <div class="abs listing-title">Amazing Family<br>Bed Room</div>
    <div class="abs listing-addr">Marlow Ln, Brookdale, CA, USA</div>
    <div class="abs details">Details</div>
    <div class="abs tag-rent">FOR RENT</div>
  </article>
  <div class="abs dots"><span></span><span></span><span class="on"></span><span></span><span></span></div>
</section>

<section class="abs features">
  <div class="abs feature-ring" style="left:260px;top:14px">
    <svg width="30" height="28" viewBox="0 0 30 28" fill="#fff"><rect x="2" y="2" width="12" height="26"/><rect x="16" y="10" width="12" height="18"/><g fill="#059fe3"><rect x="5" y="6" width="2.5" height="3"/><rect x="9" y="6" width="2.5" height="3"/><rect x="5" y="12" width="2.5" height="3"/><rect x="9" y="12" width="2.5" height="3"/><rect x="5" y="18" width="2.5" height="3"/><rect x="9" y="18" width="2.5" height="3"/><rect x="19" y="14" width="2.5" height="3"/><rect x="23" y="14" width="2.5" height="3"/><rect x="20" y="21" width="4" height="7"/></g></svg>
  </div>
  <div class="abs feature-title" style="left:138px;top:118px">Modern Rooms</div>
  <div class="abs feature-text" style="left:152px;top:145px">Vestibulum at magna tellus. Vivamus is<br>amus porta ligula in orc</div>

  <div class="abs feature-ring" style="left:559px;top:14px">
    <svg width="30" height="30" viewBox="0 0 30 30" fill="none" stroke="#fff" stroke-width="3.2" stroke-linecap="round"><line x1="5" y1="25" x2="23" y2="7"/><line x1="6" y1="6" x2="25" y2="25"/><path d="M20 4l6 6" stroke-width="4"/><path d="M3 9l6-6" stroke-width="4"/></svg>
  </div>
  <div class="abs feature-title" style="left:462px;top:119px">Fire Protection Services</div>
  <div class="abs feature-text" style="left:462px;top:146px">Vestibulum at magna tellus. Vivamus is<br>amus porta ligula in orc</div>

  <div class="abs feature-ring" style="left:859px;top:14px">
    <svg width="30" height="28" viewBox="0 0 30 28" fill="none" stroke="#fff" stroke-width="2.4"><path d="M4 13L15 3l11 10"/><path d="M8 11v14h14V11"/><path d="M12 25v-7h6v7"/><path d="M2 5v20M28 5v20" stroke-width="1.4"/></svg>
  </div>
  <div class="abs feature-text" style="left:799px;top:146px;width:40px;text-align:left;overflow:hidden;white-space:nowrap">We have</div>
</section>

<h2 class="abs section-title">Newest Bedroom</h2>
<p class="abs section-sub">Absolutely Stunning Design and Functionality</p>

<div class="abs room-photo" style="left:160px;width:429px;background:linear-gradient(160deg,#6b4a2a 0%,#c9a36a 45%,#e8d3a6 70%,#7a5b3a 100%)" role="img" aria-label="Photo of a warm-toned bedroom with wood panelling">
  <div class="abs tag-green">FOR RENT</div>
</div>
<div class="abs room-photo" style="left:610px;width:240px;background:linear-gradient(160deg,#dfe3e6 0%,#b8c2c7 60%,#8fa5ab 100%)" role="img" aria-label="Photo of a bright modern bedroom with a teal chair"></div>

<aside class="abs chat">
  <div class="abs chat-head">
    <div class="abs chat-title">Lodgivo Could Live Chat</div>
    <svg class="abs" style="left:274px;top:21px" width="60" height="22" viewBox="0 0 60 22" stroke="#fff" stroke-width="2.2"><line x1="2" y1="20" x2="24" y2="20"/><line x1="41" y1="2" x2="58" y2="19"/><line x1="58" y1="2" x2="41" y2="19"/></svg>
  </div>
  <div class="abs chat-body">
    <div class="abs bubble them" style="top:43px">Hi!</div>
    <svg class="abs" style="left:27px;top:33px" width="10" height="11" viewBox="0 0 10 11"><path d="M0 0L10 11H0z" fill="#c9c9d1"/></svg>
    <div class="abs bubble them" style="top:97px">How may I help you?</div>
    <div class="abs bubble me" style="top:148px">Hello!</div>
    <svg class="abs" style="left:292px;top:187px" width="9" height="10" viewBox="0 0 9 10"><path d="M0 0H9V10z" fill="#4cb3f5"/></svg>
    <div class="abs bubble me" style="top:204px">I need help with the design.</div>
  </div>
  <div class="abs scroll-track"></div>
  <div class="abs scroll-thumb"></div>
  <svg class="abs" style="left:22px;top:386px" width="20" height="18" viewBox="0 0 20 18" fill="#555"><path d="M1 6h4l6-5v16l-6-5H1z"/><path d="M14 5q3 4 0 8M16.5 2.5q5 6.5 0 13" fill="none" stroke="#555" stroke-width="1.6"/></svg>
  <svg class="abs" style="left:50px;top:383px" width="14" height="22" viewBox="0 0 14 22" fill="#555"><rect x="4" y="1" width="6" height="12" rx="3"/><path d="M1.5 9q0 6 5.5 6t5.5-6" fill="none" stroke="#555" stroke-width="1.8"/><rect x="6" y="15" width="2" height="5"/><rect x="3" y="19.5" width="8" height="2"/></svg>
  <div class="abs chat-input">
    <span class="abs placeholder">Type your message here...</span>
    <div class="abs send"><svg width="30" height="18" viewBox="0 0 30 18"><path d="M1 1l28 8L1 17l5-8z" fill="#fff"/></svg></div>
  </div>
</aside>

</body>
</html>
```